Expedition Cruise Sales Website for the Polar Regions (Antarctica & Arctic)

This will be a website for selling cruises.
This site should have a homepage, a ship page, destinations, and itineraries.
I have created a file specifying each page, and it is attached.
Pages:
1. Home
2. Cruise Lines
- 2.1 Ships
3. Destinations
- 3.1 Region - 3.2 Country - 3.3 City
4. Itineraries
- 4.1 Itinerary
5. Blog / Travel Tips 6. About Us
7. Contact
Please take a look on the attached pdf
Target Market(s)
Expedition Travelers
Coding
Coded - Design and coding required
Number of Pages Required
5+ page
Font styles to use
Look and feel
Each slider illustrates characteristics of the customer's brand and the style your logo design should communicate.

```html
<!DOCTYPE html>
<html lang="en">
<head>
<meta charset="utf-8">
<title>Boreala.co – Find Your Cruise</title>
<link href="https://fonts.googleapis.com/css2?family=Abril+Fatface&family=Titillium+Web:ital,wght@0,400;0,600;0,700;1,400&display=swap" rel="stylesheet">
<style>
:root{
  --blue:#2c5fa8;
  --blue-dark:#1f4a8c;
  --ink:#111;
  --text:#333;
  --soft:#f0f0f0;
  --line:#d9d9d9;
  --footer:#1e1e1e;
  --white:#fff;
}
*{box-sizing:border-box;margin:0;padding:0}
html,body{width:1200px;height:4003px;overflow:hidden}
body{font-family:"Titillium Web",sans-serif;color:var(--text);background:var(--white);position:relative}
.abs{position:absolute}
.display{font-family:"Abril Fatface",serif;font-weight:400;color:var(--ink);text-transform:uppercase;letter-spacing:-.5px}
.display span{color:var(--blue)}
.lede{font-style:italic;font-size:16px;color:var(--text);white-space:nowrap}

/* top bar */
.topbar{left:0;top:0;width:1200px;height:40px;background:var(--blue);color:#fff;font-size:12px;text-align:center;line-height:40px}

/* hero */
.hero{left:0;top:40px;width:1200px;height:594px}
.hero-photo{left:0;top:0;width:1200px;height:594px;background:linear-gradient(180deg,#e6e4f3 0%,#dcdff0 35%,#cdd4e8 55%,#a9b9d6 72%,#6f8bb4 86%,#3c5e92 100%)}
.brand{left:104px;top:14px;display:flex;flex-direction:column;align-items:center;gap:6px}
.brand-mark{width:40px;height:40px;border-radius:50%;background:var(--blue)}
.brand-name{font-size:28px;font-weight:700;color:var(--blue);line-height:1}
.nav{left:325px;top:40px;display:flex;gap:30px;font-size:15px;font-weight:600;color:#222}
.nav .active{color:var(--blue);border-bottom:2px solid var(--blue);padding-bottom:2px}
.account{left:1048px;top:28px;width:48px;height:48px;border:2px solid #1d2a44;border-radius:50%;display:flex;align-items:center;justify-content:center}
.hero-title{left:0;width:1200px;top:130px;text-align:center;font-family:"Abril Fatface",serif;font-weight:400;font-size:68px;line-height:1.1;color:#111}
.hero-sub{left:0;width:1200px;top:218px;text-align:center;font-style:italic;font-size:18px;color:var(--blue-dark);letter-spacing:.5px}
.search{top:278px;height:47px;background:#fff;border-radius:3px;font-size:13px;color:#666;display:flex;align-items:center;justify-content:space-between;padding:0 12px}
.search-btn{left:892px;top:278px;width:148px;height:47px;background:var(--blue);color:#fff;font-weight:700;font-size:16px;border-radius:3px;display:flex;align-items:center;justify-content:center;gap:6px}

/* featured */
.section-title{font-size:50px;line-height:1;white-space:nowrap}
.offer{top:838px;width:314px;height:390px;background:#fff;border:1px solid var(--line);box-shadow:0 2px 6px rgba(0,0,0,.08);text-align:center}
.offer .pic{height:222px}
.offer h3{font-size:17px;font-weight:700;color:#111;margin-top:24px}
.offer p{font-size:15px;line-height:22px;margin:8px 26px 0}
.offer .price{margin-top:10px;font-size:15px}
.offer .price .old{color:var(--blue);margin-right:8px}
.offer .price b{color:#222}
.offer.is-active{background:var(--blue);border-color:var(--blue-dark)}
.offer.is-active h3,.offer.is-active p,.offer.is-active .price .old,.offer.is-active .price b{color:#fff}

/* destinations */
.band-soft{left:0;top:1320px;width:1200px;height:598px;background:var(--soft)}
.dest{top:1506px;width:308px;height:346px;background:#fff}
.dest .pic{height:267px}
.dest .label{height:79px;display:flex;align-items:center;justify-content:center;font-weight:700;font-size:17px;color:#111}
.dest.is-active .label{background:var(--blue);color:#fff}

/* cruise lines */
.arrow{top:2029px;width:38px;height:38px;border-radius:50%;display:flex;align-items:center;justify-content:center}
.line-card{top:2130px;width:271px;height:284px}
.line-card.featured{background:#3a3a3a;border:4px solid #222;display:flex;flex-direction:column;align-items:center;color:#fff;text-align:center}
.line-logo{margin-top:22px;width:104px;height:104px;border-radius:50%;background:#fff;display:flex;align-items:center;justify-content:center;font-size:15px;color:#c0392b;font-weight:600}
.stars{color:#e8a020;font-size:16px;letter-spacing:2px;margin-top:10px}
.line-card.featured p{font-size:14px;line-height:21px;margin:4px 30px 0}

/* testimonials */
.testi{left:0;top:2505px;width:1200px;height:479px;background:linear-gradient(180deg,#2f62aa,#2a5a9f)}
.testi h2{left:0;width:1200px;top:68px;text-align:center;color:#fff;font-size:50px;line-height:1}
.avatar{left:562px;top:160px;width:76px;height:76px;border-radius:50%;background:linear-gradient(135deg,#d9c2a8,#6b4e3a);border:3px solid #fff}
.quote{left:200px;width:800px;top:270px;text-align:center;color:#fff;font-size:16px;line-height:24px}
.who{left:0;width:1200px;top:330px;text-align:center;color:#fff;font-size:24px}
.who-stars{left:0;width:1200px;top:366px;text-align:center;color:#fff;font-size:13px;letter-spacing:2px}
.dots{left:547px;top:398px;display:flex;gap:10px;align-items:center}
.dots i{display:block;width:26px;height:2px;background:rgba(255,255,255,.6)}
.dots i.on{width:42px;height:3px;background:#fff}

/* contact */
.field{border:1.5px solid #333;border-radius:3px;font-size:13px;color:#333;padding:14px 13px}
.btn{top:3484px;height:47px;border-radius:3px;display:flex;align-items:center;justify-content:center;font-weight:700;font-size:15px}
.btn-primary{left:458px;width:129px;background:var(--blue);color:#fff}
.btn-chat{left:601px;width:142px;border:2px solid var(--blue);color:#111;gap:8px}
.btn-chat i{width:30px;height:30px;border-radius:50%;background:#2bb34a;display:block}

/* footer */
.footer{left:0;top:3624px;width:1200px;height:379px;background:var(--footer);color:#fff}
.f-brand{left:105px;top:60px;display:flex;flex-direction:column;align-items:center;gap:14px;width:270px}
.f-brand .brand-mark{width:70px;height:70px;background:#fff}
.f-brand .brand-name{color:#fff;font-size:52px}
.social{top:244px;width:44px;height:44px;border-radius:50%;border:1.5px solid #fff}
.social.on{background:var(--blue);border-color:var(--blue)}
.f-col h4{font-size:20px;font-weight:600;margin-bottom:14px}
.f-links{list-style:none;font-size:15px;line-height:26.4px}
.f-contact{display:flex;gap:12px;margin-bottom:18px}
.f-contact .ic{width:40px;height:40px;border-radius:50%;background:var(--blue);display:flex;align-items:center;justify-content:center;flex:none}
.f-contact b{font-size:13px;display:block;line-height:18px}
.f-contact span{font-size:14px;line-height:19px}
.news-input{left:887px;top:99px;width:210px;height:44px;background:#fff;border-radius:3px;color:#888;font-size:12px;padding:13px 12px}
.news-btn{left:887px;top:157px;width:131px;height:46px;background:var(--blue);border:1px solid #fff;border-radius:3px;font-weight:700;font-size:15px;display:flex;align-items:center;justify-content:center}
.f-rule{left:103px;top:323px;width:994px;height:1px;background:#555}
.copy{left:0;width:1200px;top:338px;text-align:center;font-size:14px}
</style>
</head>
<body>

<div class="abs topbar">Let us whisk you away to paradise aboard our luxurious cruises! Buy cruise tickets to the best destinations on Boreala.co</div>

<header class="abs hero">
  <div class="abs hero-photo" role="img" aria-label="Large white cruise ship sailing on a calm blue sea under a pale evening sky"></div>
  <div class="abs brand"><div class="brand-mark"></div><div class="brand-name">Boreala.co</div></div>
  <nav class="abs nav">
    <span class="active">Home</span><span>Cruise Lines</span><span>Destinations</span><span>Itineraries</span><span>Blog/TravelTips</span><span>About Us</span><span>Contact</span>
  </nav>
  <div class="abs account"><svg width="18" height="18" viewBox="0 0 18 18" fill="none" stroke="#1d2a44" stroke-width="2"><circle cx="9" cy="6" r="3.5"/><path d="M2.5 16c1-3.5 3.5-5 6.5-5s5.5 1.5 6.5 5z"/></svg></div>
  <h1 class="abs hero-title">Find Your Cruise</h1>
  <p class="abs hero-sub">Thousands Of Cruise Travelers Have Experienced Their Best Time With Us</p>
  <div class="abs search" style="left:160px;width:322px">Where Do Your To Go? <span>⇕</span></div>
  <div class="abs search" style="left:491px;width:135px">When? <span style="width:12px;height:11px;background:#aaa;display:inline-block"></span></div>
  <div class="abs search" style="left:685px;width:198px">How Long? <span>⇕</span></div>
  <div class="abs search-btn">Search <svg width="15" height="15" viewBox="0 0 15 15" fill="none" stroke="#fff" stroke-width="2.2"><circle cx="6" cy="6" r="4.5"/><path d="M9.5 9.5L14 14"/></svg></div>
</header>

<!-- Featured offers -->
<h2 class="abs display section-title" style="left:103px;top:718px">Featured <span>Offers</span></h2>
<p class="abs lede" style="left:104px;top:780px">Get ready to set sail to the most exotic cruise destinations with our unparalleled cruise deals. Book a cruise online on Boreala.co</p>
<article class="abs offer" style="left:103px">
  <div class="pic" role="img" aria-label="Cruise boarding passes on a wooden table" style="background:linear-gradient(135deg,#8a5a3a,#1f3563 55%,#c9d3e4)"></div>
  <h3>BEST ANTARCTIC CRUISES</h3>
  <p>Lorem ipsum dolor sit amet, ectetur adipiscing elit,dolor sit amet.</p>
  <div class="price"><span class="old">$55.00</span><b>$67.00</b></div>
</article>
<article class="abs offer is-active" style="left:441px">
  <div class="pic" role="img" aria-label="Cruise ship at sea seen from above" style="background:linear-gradient(160deg,#5b7ea6,#2e4f74 60%,#dfe4ea)"></div>
  <h3>TOP GALÁPAGOS CRUISES</h3>
  <p>Lorem ipsum dolor sit amet, ectetur adipiscing elit,dolor sit amet.</p>
  <div class="price"><span class="old">$50.00</span><b>$61.00</b></div>
</article>
<article class="abs offer" style="left:782px">
  <div class="pic" role="img" aria-label="Harbor with boats and a boat ride sign" style="background:linear-gradient(135deg,#4a86c6,#a8c8e8 50%,#2a4a7a)"></div>
  <h3>LAST-MINUTE DEALS</h3>
  <p>Lorem ipsum dolor sit amet, ectetur adipiscing elit,dolor sit amet.</p>
  <div class="price"><span class="old">$45.00</span><b>$59.00</b></div>
</article>

<!-- Destinations -->
<div class="abs band-soft"></div>
<h2 class="abs display section-title" style="left:0;width:1200px;text-align:center;top:1378px">Highlighted <span>Destinations</span></h2>
<p class="abs lede" style="left:0;width:1200px;text-align:center;top:1439px">Let us whisk you away to paradise aboard our luxurious cruises! Buy cruise tickets to the best destinations on Boreala.co</p>
<div class="abs dest" style="left:103px">
  <div class="pic" role="img" aria-label="Cruise ship ticket on white fabric" style="background:linear-gradient(135deg,#c9d4e2,#e9ecf2 50%,#b7a58c)"></div>
  <div class="label">REGION</div>
</div>
<div class="abs dest is-active" style="left:446px">
  <div class="pic" role="img" aria-label="Illustrated cruise ticket with palm trees and sea" style="background:linear-gradient(160deg,#f0e0b8,#f2f2ee 50%,#4aa3a8)"></div>
  <div class="label">COUNTRY</div>
</div>
<div class="abs dest" style="left:788px">
  <div class="pic" role="img" aria-label="Stack of printed cruise tickets" style="background:linear-gradient(180deg,#2a5aa0,#5fa8d8 40%,#1e4080)"></div>
  <div class="label">CITY</div>
</div>

<!-- Cruise lines -->
<h2 class="abs display section-title" style="left:103px;top:2003px">Top <span>Cruise Lines</span></h2>
<p class="abs lede" style="left:103px;top:2067px">Experience unparalleled luxury and adventure with our top cruise lines featured on Boreala.co</p>
<div class="abs arrow" style="left:1046px;background:var(--blue)"><svg width="12" height="12" viewBox="0 0 12 12" fill="none" stroke="#fff" stroke-width="2"><path d="M8 1L3 6l5 5"/></svg></div>
<div class="abs arrow" style="left:1106px;border:1.5px solid var(--blue)"><svg width="12" height="12" viewBox="0 0 12 12" fill="none" stroke="#2c5fa8" stroke-width="2"><path d="M4 1l5 5-5 5"/></svg></div>
<div class="abs line-card" style="left:104px;background:linear-gradient(160deg,#8fb6d6,#3f6b94 50%,#1f3e66)" role="img" aria-label="Cruise ship deck with pools seen from above"></div>
<div class="abs line-card featured" style="left:400px">
  <div class="line-logo">Harborline</div>
  <div class="stars">★★★★★</div>
  <p>Lorem ipsum dolor sit amet, consectetur adipiscing elit,Quis ipsum suspendisse</p>
</div>
<div class="abs line-card" style="left:697px;background:linear-gradient(170deg,#b9c9da,#5d7fa3 50%,#2b4c73)" role="img" aria-label="Cruise ship sailing toward the viewer"></div>
<div class="abs line-card" style="left:992px;width:208px;background:linear-gradient(170deg,#d3cde0,#8a9cbc 50%,#3c5a84)" role="img" aria-label="Cruise ship at sea under a pink sky"></div>

<!-- Testimonials -->
<section class="abs testi">
  <h2 class="abs display">Customer Testimonials</h2>
  <div class="abs avatar" role="img" aria-label="Customer portrait"></div>
  <p class="abs quote">Lorem ipsum dolor sit amet, consectetur iscng elit, sed do eiusmod tempor incididunt ut bore et dolore magna qua. Quis ipsum suspendisse lices gravida&nbsp; eiusmod tempor incididunt ut bore et.</p>
  <div class="abs who">Dana R</div>
  <div class="abs who-stars">★★★★★</div>
  <div class="abs dots"><i></i><i class="on"></i><i></i></div>
</section>

<!-- Contact -->
<h2 class="abs display section-title" style="left:0;width:1200px;text-align:center;top:3064px">Contact <span>Us</span></h2>
<div class="abs field" style="left:103px;top:3159px;width:486px;height:54px">First Name</div>
<div class="abs field" style="left:609px;top:3159px;width:488px;height:54px">Last Name</div>
<div class="abs field" style="left:103px;top:3232px;width:486px;height:54px">Email</div>
<div class="abs field" style="left:609px;top:3232px;width:488px;height:54px">Phone</div>
<div class="abs field" style="left:103px;top:3307px;width:994px;height:149px">Message</div>
<div class="abs btn btn-primary">Submit</div>
<div class="abs btn btn-chat"><i></i>Chat</div>

<!-- Footer -->
<footer class="abs footer">
  <div class="abs f-brand"><div class="brand-mark"></div><div class="brand-name">Boreala.co</div></div>
  <div class="abs social on" style="left:152px" aria-label="Social profile"></div>
  <div class="abs social" style="left:210px" aria-label="Social profile"></div>
  <div class="abs social" style="left:267px" aria-label="Social profile"></div>

  <div class="abs f-col" style="left:421px;top:60px">
    <h4>Quick Links</h4>
    <ul class="f-links"><li>Home</li><li>Cruise Lines</li><li>Destinations</li><li>Itineraries</li><li>Blog/TravelTips</li><li>About Us</li><li>Faq</li><li>Contact</li></ul>
  </div>

  <div class="abs f-col" style="left:608px;top:58px;width:260px">
    <h4>Contact Us</h4>
    <div class="f-contact"><div class="ic"><svg width="18" height="18" viewBox="0 0 18 18" fill="#fff"><path d="M4 1.5l3 3-2 2c1 2.5 3 4.5 5.5 5.5l2-2 3 3-2 2.5C8 15 3 10 1.5 3.5z"/></svg></div><div><b>PHONE NO:</b><span>+1(555) 014-2290</span></div></div>
    <div class="f-contact"><div class="ic"><svg width="18" height="14" viewBox="0 0 18 14" fill="#fff"><path d="M1 1h16v12H1z"/><path d="M1 1l8 6 8-6" stroke="#2c5fa8" stroke-width="1.6" fill="none"/></svg></div><div><b>EMAIL:</b><span>hello@boreala-voyages.com</span></div></div>
    <div class="f-contact"><div class="ic"><svg width="14" height="18" viewBox="0 0 14 18" fill="#fff"><path d="M7 0a7 7 0 0 0-7 7c0 5 7 11 7 11s7-6 7-11a7 7 0 0 0-7-7zm0 10a3 3 0 1 1 0-6 3 3 0 0 1 0 6z"/></svg></div><div><b>LOCATION:</b><span>Lorem ipsum dolor sit<br>amet,consetur,USA</span></div></div>
  </div>

  <div class="abs f-col" style="left:883px;top:58px"><h4>Our Newsletter</h4></div>
  <div class="abs news-input">Email Adress</div>
  <div class="abs news-btn">Subscribe</div>

  <div class="abs f-rule"></div>
  <div class="abs copy">Copyright © 2025 Boreala.co | All Rights Reserved.Privacy Policy &amp; Terms Of Use</div>
</footer>

</body>
</html>
```